Meadowfield Baptist Church Banner Design

Designing 6 banners (3 + 3 that will hang on opposite sides of our auditorium) that are 10 feet long by 4 feet wide.

Use our branding guide - specifically item 4 (vertical logo) and item 5 (icon logo).

Design elements found in our KINDLE booklet, we would like to see designs that utilize the white, green and blue colour palettes but NOT the grey. Other colours may be incorporated (e.g. coral).

We are looking for 3 banner designs that would match on either side of the auditorium, the first banner incorporating the word "TRUTH", the second incorporating the word "LOVE", and the third incorporating the word "MISSION".

We interested in incorporating graphics such as trees or outdoor themes.

Font styles to use
Other font styles liked:
• Montserrat

Colors
34a7d7
00a990
f47c35

Requirements
Must have
• Banner Type #1 include the word "TRUTH"
Banner Type #2 include the word "LOVE"
Banner Type #3 include the word "MISSION"

Colour scheme must include CMYK 54 / 5 / 16 / 0 (which is available in the branding guide.) We have selected the three colours, included below in the brief.

From the branding guide - utilize #5 (icon) for the banner.

UPDATE: After reviewing the initial submissions, we are asking for designs that ONLY incorporate #5 - the ICON logo for the banners.
Nice to have
• It would be nice to have some creativity with the colour ... though a more minimalistic style is preferred.

Graphic adaptations such as trees in the background would be of interest.
Should not have
• Colour scheme should not be gray scale.

The banners should NOT be too busy.

Scripture verses (written out) are not necessary.

```html
<!DOCTYPE html>
<html lang="en">
<head>
<meta charset="utf-8">
<title>Meadowfield Baptist Church – Truth Banner</title>
<link rel="stylesheet" href="https://fonts.googleapis.com/css2?family=Montserrat:wght@600;700;800&family=Yellowtail&family=Tinos:ital@1&display=swap">
<style>
  :root {
    --banner-bg: #ffffff;
    --brand-blue: #34a7d7;
    --brand-green: #00a990;
    --ink: #000000;
    --church-teal: #6cc3d5;
  }
  html, body {
    margin: 0;
    padding: 0;
    overflow: hidden;
    background: var(--banner-bg);
  }
  .banner {
    position: relative;
    width: 1200px;
    height: 3067px;
    background: var(--banner-bg);
    overflow: hidden;
  }
  .banner > * {
    position: absolute;
    left: 0;
    width: 100%;
    text-align: center;
    margin: 0;
  }
  .headline-word {
    font-family: "Montserrat", sans-serif;
    line-height: 1;
  }
  .word-i {
    top: 325px;
    font-size: 560px;
    font-weight: 800;
    color: var(--brand-blue);
  }
  .word-am {
    top: 815px;
    font-size: 390px;
    font-weight: 800;
    letter-spacing: -12px;
    color: var(--brand-blue);
  }
  .word-the {
    top: 1195px;
    font-family: "Yellowtail", cursive;
    font-size: 200px;
    line-height: 1;
    color: var(--brand-green);
    transform: rotate(-4deg);
  }
  .word-truth {
    top: 1300px;
    font-size: 380px;
    font-weight: 700;
    letter-spacing: -6px;
    color: var(--ink);
  }
  .scripture-ref {
    top: 1700px;
    font-family: "Tinos", serif;
    font-style: italic;
    font-size: 88px;
    line-height: 1;
    color: var(--brand-green);
  }
  .church-mark {
    top: 2210px;
    height: 450px;
  }
  .church-mark svg {
    display: block;
    margin: 0 auto;
  }
  .church-name {
    top: 2720px;
    font-family: "Montserrat", sans-serif;
    font-weight: 700;
    color: var(--church-teal);
    line-height: 1.15;
  }
  .church-name .line-main {
    display: block;
    font-size: 96px;
    letter-spacing: 2px;
  }
  .church-name .line-sub {
    display: block;
    font-size: 58px;
    letter-spacing: 4px;
  }
</style>
</head>
<body>
  <main class="banner">
    <p class="headline-word word-i">I</p>
    <p class="headline-word word-am">AM</p>
    <p class="word-the">the</p>
    <p class="headline-word word-truth">truth</p>
    <p class="scripture-ref">John 14:6</p>

    <div class="church-mark" aria-hidden="true">
      <svg width="450" height="450" viewBox="0 0 450 450">
        <circle cx="225" cy="225" r="200" fill="none" stroke="var(--church-teal)" stroke-width="28"/>
      </svg>
    </div>
    <p class="church-name">
      <span class="line-main">MEADOWFIELD</span>
      <span class="line-sub">BAPTIST CHURCH</span>
    </p>
  </main>
</body>
</html>
```